Single-sided business card for restaurant velmora with new logo made on this site

Business card options with new logo including restaurant name, address, phone number and website. This business card is single-sided only and will be presented at the hostess desk for clients to take. I would like to see options based on a cream card background, a white card background, a yellow card background and a burgundy colored background. It needs to be elegant and traditional.

Target Market(s)

local and international crowd

Industry/Entity Type

restaurant

Contact Information for Business Card

address, website and phone number

Font styles to use
Serif

Colors
EE7325
F08F49
F5BC92
FAE3D3
FDF4ED

Requirements
Must have
• new logo, address, phone number, website
Should not have
• more than three colors

```html
<!DOCTYPE html>
<html lang="es">
<head>
<meta charset="utf-8">
<title>Velmora — Tarjeta de presentación</title>
<link rel="stylesheet" href="https://fonts.googleapis.com/css2?family=Marcellus+SC&display=swap">
<style>
  :root {
    --backdrop: #7d6148;
    --card: #fbfbfa;
    --gold: #eaa723;
    --brown: #3b1a1c;
  }
  * { margin: 0; padding: 0; box-sizing: border-box; }
  html, body { width: 900px; height: 1200px; overflow: hidden; }
  body {
    background: var(--backdrop);
    position: relative;
    font-family: "Marcellus SC", "Times New Roman", serif;
  }
  .card {
    position: absolute;
    left: 73px;
    width: 777px;
    background: var(--card);
  }
  .card--gold-text { top: 130px; height: 452px; }
  .card--brown-text { top: 618px; height: 459px; }

  .brand {
    position: absolute;
    left: 96px;
    top: 128px;
    width: 194px;
    text-align: center;
  }
  .brand__square {
    display: block;
    width: 112px;
    height: 112px;
    margin: 0 auto 14px;
    background: var(--gold);
  }
  .brand__name {
    font-size: 38px;
    letter-spacing: 5px;
    color: var(--brown);
    line-height: 1;
  }

  .divider {
    position: absolute;
    left: 366px;
    top: 73px;
    width: 2px;
    height: 306px;
  }
  .details {
    position: absolute;
    left: 427px;
    top: 78px;
    font-size: 21px;
    line-height: 31px;
    letter-spacing: 0.3px;
  }
  .details__rule {
    width: 92px;
    height: 2px;
    margin: 18px 0 19px;
  }
  .details__web { font-size: 19px; }

  .card--gold-text .details { color: var(--gold); }
  .card--gold-text .details__rule,
  .card--gold-text .divider { background: var(--brown); }

  .card--brown-text .details { color: var(--brown); }
  .card--brown-text .details__rule,
  .card--brown-text .divider { background: var(--gold); }
  .card--brown-text .brand { top: 130px; }
  .card--brown-text .divider { top: 75px; height: 309px; }
  .card--brown-text .details { top: 80px; }
</style>
</head>
<body>
  <section class="card card--gold-text">
    <div class="brand">
      <span class="brand__square"></span>
      <p class="brand__name">VELMORA</p>
    </div>
    <div class="divider"></div>
    <div class="details">
      <p>Restaurant Velmora</p>
      <div class="details__rule"></div>
      <p>Calle Jacaranda 415</p>
      <p>Puerto Ángel Sur,</p>
      <p>Oaxaca CP 70912</p>
      <div class="details__rule"></div>
      <p>Reservaciones</p>
      <p>958-314-2270</p>
      <p class="details__web">www.velmora.com.mx</p>
    </div>
  </section>

  <section class="card card--brown-text">
    <div class="brand">
      <span class="brand__square"></span>
      <p class="brand__name">VELMORA</p>
    </div>
    <div class="divider"></div>
    <div class="details">
      <p>Restaurant Velmora</p>
      <div class="details__rule"></div>
      <p>Calle Jacaranda 415</p>
      <p>Puerto Ángel Sur,</p>
      <p>Oaxaca CP 70912</p>
      <div class="details__rule"></div>
      <p>Reservaciones</p>
      <p>958-314-2270</p>
      <p class="details__web">www.velmora.com.mx</p>
    </div>
  </section>
</body>
</html>
```